Brightmoor Lift Inc Website Deisgn

We are a new small elevator contracting company.
We would like a full website designed similar to
http://pellingtonlifts.com or https://www.northvalelifting.ca/
In addition to contents found on the above webpages.. we would like a section for project gallery etc.... have fun with it ... make it professional

Target Market(s)

Elevator Consultants - Property managers - Condo Boards - Commercial office buildings

Coding

Number of Pages Required

5+ page

Requirements
Must have
• Navigation Bar.. Be view able via mobile ..Should be pictures of Tall Office buildings in background.. Toronto city skyline etc....

Have Fun!

```html
<!DOCTYPE html>
<html lang="en">
<head>
<meta charset="utf-8">
<title>Brightmoor Lift Inc</title>
<link rel="stylesheet" href="https://fonts.googleapis.com/css2?family=Merriweather:wght@400;700&family=Open+Sans:ital,wght@0,400;0,600;1,400&display=swap">
<style>
:root{
  --orange:#e8520f;
  --blue:#3f6fa8;
  --dark:#242226;
  --nav:#222122;
  --grey:#d6d5d6;
  --text:#2a2a2a;
  --muted:#777;
  --white:#fff;
}
*{box-sizing:border-box;margin:0;padding:0}
html,body{width:1200px;height:4253px;overflow:hidden}
body{position:relative;font-family:"Open Sans",sans-serif;color:var(--text);background:var(--white)}
.abs{position:absolute}
.serif{font-family:"Merriweather",serif}
.btn{position:absolute;display:flex;align-items:center;justify-content:center;gap:22px;background:var(--orange);color:var(--white);border-radius:26px;font-size:15px;letter-spacing:.5px}
.btn svg{width:26px;height:14px}
.photo{position:absolute}

/* header */
.tagline{left:135px;top:30px;font-size:17px;color:#333}
.brand{left:450px;top:26px;width:300px;text-align:center;white-space:nowrap;font-size:22px;font-weight:600;color:#222;letter-spacing:1px;line-height:34px}
.contact{left:815px;font-size:13px;color:#333;display:flex;align-items:center;gap:14px}
.contact svg{width:16px;height:16px}
.nav{left:0;top:88px;width:1200px;height:52px;background:var(--nav);display:flex;justify-content:center;align-items:center;gap:40px;color:var(--white);font-size:15px}

/* hero */
.hero{left:0;top:140px;width:1200px;height:600px;background:linear-gradient(180deg,#6f8aa6 0%,#c6a88b 30%,#8d7463 55%,#3e3a3c 100%)}
.hero-title{left:0;top:300px;width:1200px;text-align:center;font-size:50px;font-weight:700;color:#1d1d1d;letter-spacing:2px}
.hero-sub{left:0;top:360px;width:1200px;text-align:center;font-size:20px;color:#1d1d1d}
.dots{display:flex;gap:12px}
.dots span{width:13px;height:13px;border:1.5px solid #888;border-radius:50%}
.dots span.on{background:var(--blue);border-color:var(--blue)}

/* about */
.h2{font-size:38px;color:#222}
.underline{position:absolute;width:30px;height:2px;background:var(--blue)}
.about-sub{left:109px;top:868px;font-size:23px;font-weight:700;color:#333}
.about-text{left:113px;top:913px;width:452px;font-size:15px;line-height:28px;color:#666;text-align:justify}
.ring-outer{left:645px;top:770px;width:434px;height:434px;border:2px solid #9fb5d3;border-radius:50%}
.ring-mid{left:655px;top:780px;width:414px;height:414px;border:5px solid var(--blue);border-radius:50%}
.ring-photo{left:665px;top:790px;width:394px;height:394px;border-radius:50%;background:radial-gradient(circle at 45% 45%,#f2f2f2,#c9c9c9 70%,#8b7261)}

/* services */
.services{left:0;top:1296px;width:1200px;height:800px;background:var(--grey)}
.center{left:0;width:1200px;text-align:center}
.card{position:absolute;top:1483px;width:318px;height:422px;background:var(--white)}
.card .pic{height:185px}
.card h3{margin-top:20px;text-align:center;font-family:"Merriweather",serif;font-weight:400;font-size:16px;color:#222;letter-spacing:.5px}
.card p{margin:18px 24px 0;font-size:13px;line-height:24px;color:#777;text-align:justify}
.card a{display:block;text-align:center;margin-top:26px;font-size:13px;color:var(--orange);text-decoration:underline}

/* gallery */
.gallery{left:0;top:2046px;width:1200px;height:990px;background:linear-gradient(180deg,#2c2b30,#3a3e46 50%,#262529)}

/* testimonials */
.tcard{position:absolute;top:3205px;width:317px;height:391px;border:2px solid var(--blue);border-radius:22px;text-align:center}
.tcard p{margin:16px 20px 0;font-size:13.5px;line-height:23px;color:#888;font-style:italic}
.tcard h4{margin-top:26px;font-family:"Merriweather",serif;font-weight:400;font-size:16px;letter-spacing:.5px;color:#222}
.tcard .role{font-size:13px;color:#777;margin-top:2px}
.tcard .avatar{width:84px;height:84px;border-radius:50%;margin:14px auto 0;background:linear-gradient(160deg,#d9c6b5,#6b5a4e)}

/* footer */
.footer{left:0;top:3700px;width:1200px;height:553px;background:var(--dark)}
.f-brand{left:111px;top:3862px;white-space:nowrap;font-size:26px;font-weight:600;letter-spacing:1px;color:var(--white);line-height:34px}
.follow{left:810px;top:3883px;display:flex;align-items:center;gap:14px;font-size:15px;color:var(--white)}
.follow span.ic{width:26px;height:26px;border-radius:50%;background:var(--white)}
.f-line{left:111px;top:3945px;width:972px;height:2px;background:var(--blue)}
.f-about{left:111px;top:3975px;width:335px;font-size:15px;line-height:28px;text-align:justify;color:var(--white)}
.f-head{font-size:14px;color:var(--white)}
.links{left:522px;top:3988px;list-style:none;font-size:15px;color:var(--white)}
.links li{height:37.5px;display:flex;gap:12px;align-items:flex-start}
.links li::before{content:"";width:5px;height:5px;border-radius:50%;background:var(--orange);margin-top:9px}
.input{left:757px;top:4003px;width:326px;height:40px;background:var(--white);border-radius:3px;font-size:14px;color:#aaa;padding:10px 14px}
.copy{left:0;top:4210px;width:1200px;text-align:center;font-size:11px;color:var(--white)}
</style>
</head>
<body>

<!-- header -->
<div class="abs tagline">ELEVATOR SERVICE SPECIALISTS</div>
<div class="abs brand">BRIGHTMOOR LIFT INC</div>
<div class="abs contact" style="top:16px"><svg viewBox="0 0 16 16"><path d="M3 1l3 3-2 2c1 2 3 4 5 5l2-2 3 3-2 3C7 15 1 9 1 3z" fill="#333"/></svg>(647) 555 0142</div>
<div class="abs contact" style="top:49px"><svg viewBox="0 0 16 16"><rect x="1.5" y="3.5" width="13" height="9" fill="none" stroke="#333"/><path d="M1.5 3.5l6.5 5 6.5-5" fill="none" stroke="#333"/></svg>mark.alden@brightmoorlift.ca</div>
<nav class="abs nav"><span>HOME</span><span>ABOUT US</span><span>OUR SERVICES</span><span>EMPLOYEES</span><span>FAQ</span><span>FREE QUOTE</span><span>CONTACT US</span></nav>

<!-- hero -->
<div class="abs hero" role="img" aria-label="City skyline of tall office towers at sunset"></div>
<div class="abs hero-title serif">BRIGHTMOOR</div>
<div class="abs hero-sub">ELEVATOR SERVICE SPECIALISTS</div>
<div class="btn" style="left:496px;top:397px;width:208px;height:50px">GET STARTED <svg viewBox="0 0 26 14"><path d="M0 7h24M18 1l6 6-6 6" fill="none" stroke="#fff" stroke-width="2"/></svg></div>
<div class="abs dots" style="left:566px;top:589px"><span></span><span></span><span class="on"></span></div>
<svg class="abs" style="left:0;top:620px" width="1200" height="120" viewBox="0 0 1200 120">
  <path d="M0 110 Q600 -20 1200 110 L1200 120 L0 120Z" fill="#3f6fa8"/>
  <path d="M0 120 L0 105 Q600 8 1200 105 L1200 120Z" fill="#fff"/>
  <path d="M40 108 Q600 -12 1160 108 Q600 20 40 108Z" fill="#3f6fa8"/>
</svg>

<!-- about -->
<div class="abs h2 serif" style="left:113px;top:800px">ABOUT US</div>
<div class="underline" style="left:113px;top:848px"></div>
<div class="abs about-sub serif">LOREM IPSUM DOLOR SIT AMET</div>
<p class="abs about-text">Lorem ipsum dolor sit amet, consectetur adipiscing elit, sed do eiusmod tempor incididunt ut labore et dolore magna aliqua. Quis ipsum suspendisse ultrices gravida. Risus commodo viverra maecenas accumsan lacus vel facilisis. t amet, consectetur adipiscing elit, sed do eiusmod tempor incididunt ut labore et dolore magna aliqua. Quis ipsum suspendisse ultrices gravida. Risus commodo viverra maecenas accumsan lacus vel facilisis.</p>
<div class="btn" style="left:109px;top:1160px;width:207px;height:50px">READ MORE <svg viewBox="0 0 26 14"><path d="M0 7h24M18 1l6 6-6 6" fill="none" stroke="#fff" stroke-width="2"/></svg></div>
<div class="abs ring-outer"></div>
<div class="abs ring-mid"></div>
<div class="abs ring-photo" role="img" aria-label="Brushed steel elevator doors in a bright white lobby"></div>

<!-- services -->
<div class="abs services"></div>
<div class="abs center h2 serif" style="top:1372px">OUR SERVICES</div>
<div class="underline" style="left:465px;top:1420px"></div>
<div class="card" style="left:111px"><div class="pic" role="img" aria-label="Finger pressing an elevator call button" style="background:linear-gradient(90deg,#b07a45,#d9b48c 50%,#c7c9cc)"></div><h3>MODERNIZATION</h3><p>Lorem ipsum dolor sitsery rtsrtio amet, consectetusrtr adipiscing elit, sed do eiusmodryd tempor incididuuiok drtnt ut laborera.</p><a>LEARN MORE</a></div>
<div class="card" style="left:441px"><div class="pic" role="img" aria-label="Technician working inside an elevator shaft" style="background:linear-gradient(180deg,#8a8d90,#5c5f63 60%,#9a9ca0)"></div><h3>SERVICE &amp; REPAIR</h3><p>Lorem ipsum dolor sitsery rtsrtio amet, consectetusrtr adipiscing elit, sed do eiusmodryd tempor incididuuiok drtnt ut laborera.</p><a>LEARN MORE</a></div>
<div class="card" style="left:771px"><div class="pic" role="img" aria-label="Hand pressing a floor button on an elevator panel" style="background:linear-gradient(135deg,#dfe3e6,#9aa1a8 60%,#4e545b)"></div><h3>MONTHLY PREVENTATIVE</h3><p>Lorem ipsum dolor sitsery rtsrtio amet, consectetusrtr adipiscing elit, sed do eiusmodryd tempor incididuuiok drtnt ut laborera.</p><a>LEARN MORE</a></div>
<div class="btn" style="left:506px;top:1938px;width:187px;height:52px">VIEW ALL <svg viewBox="0 0 26 14"><path d="M0 7h24M18 1l6 6-6 6" fill="none" stroke="#fff" stroke-width="2"/></svg></div>

<!-- gallery -->
<div class="abs gallery" role="img" aria-label="Dark backdrop of high-rise towers"></div>
<svg class="abs" style="left:0;top:2040px" width="1200" height="100" viewBox="0 0 1200 100">
  <path d="M0 0 L1200 0 L1200 20 Q600 150 0 20Z" fill="#d6d5d6"/>
  <path d="M40 6 Q600 110 1160 6 Q600 82 40 6Z" fill="#3f6fa8"/>
</svg>
<div class="abs center h2 serif" style="top:2190px;color:#fff">GALLERY</div>
<div class="underline" style="left:518px;top:2238px"></div>
<div class="photo" role="img" aria-label="Aerial view of a downtown waterfront and stadium" style="left:111px;top:2287px;width:318px;height:218px;background:linear-gradient(180deg,#a9c3dc,#6d7b86 55%,#4d5660)"></div>
<div class="photo" role="img" aria-label="Grey elevator doors beside a stairwell" style="left:441px;top:2287px;width:318px;height:340px;background:linear-gradient(90deg,#e8e8e8,#8d8f92 50%,#e0e0e0)"></div>
<div class="photo" role="img" aria-label="Access card held against an elevator keypad" style="left:771px;top:2287px;width:318px;height:218px;background:linear-gradient(135deg,#7a5e4a,#a89484 50%,#4e3e34)"></div>
<div class="photo" role="img" aria-label="Worker climbing inside a lift shaft" style="left:111px;top:2515px;width:318px;height:293px;background:linear-gradient(180deg,#6c6b66,#8f8d86 50%,#3d3c39)"></div>
<div class="photo" role="img" aria-label="Pair of steel elevator doors in a lobby" style="left:441px;top:2637px;width:318px;height:171px;background:linear-gradient(180deg,#c9c4bb,#8f887d 60%,#6c665d)"></div>
<div class="photo" role="img" aria-label="Finger pressing illuminated floor buttons" style="left:771px;top:2515px;width:318px;height:293px;background:linear-gradient(90deg,#e6e8ea,#a8adb2 50%,#5e646a)"></div>
<div class="btn" style="left:506px;top:2848px;width:187px;height:52px">VIEW ALL <svg viewBox="0 0 26 14"><path d="M0 7h24M18 1l6 6-6 6" fill="none" stroke="#fff" stroke-width="2"/></svg></div>
<svg class="abs" style="left:0;top:2920px" width="1200" height="120" viewBox="0 0 1200 120">
  <path d="M0 120 L0 105 Q600 -30 1200 105 L1200 120Z" fill="#3f6fa8"/>
  <path d="M0 120 L0 100 Q600 10 1200 100 L1200 120Z" fill="#fff"/>
  <path d="M0 120 L1200 120 L1200 106 Q600 14 0 106Z" fill="#fff"/>
  <path d="M40 106 Q600 -10 1160 106 Q600 18 40 106Z" fill="#3f6fa8"/>
</svg>

<!-- testimonials -->
<div class="abs center h2 serif" style="top:3080px">TESTIMONIALS</div>
<div class="underline" style="left:460px;top:3128px"></div>
<div class="tcard" style="left:111px"><p>Sed ut perspiciatis unde omnis iste natus error sit ser voluptatem seraccusantium doloremque laudantium, ser totam rem aperiam, eaque seryu ipsa quae ab illo inventore veritatis et quasi architecto beatae vitae dicta sunt explicabo. Nemo enim ipsam voluptatem quia voluptas sit aspernatur aut odit aut.</p><h4>OWEN BARCLAY</h4><div class="role">CEO, LOFTWELL</div><div class="avatar" role="img" aria-label="Client portrait"></div></div>
<div class="tcard" style="left:441px"><p>Sed ut perspiciatis unde omnis iste natus error sit ser voluptatem seraccusantium doloremque laudantium, ser totam rem aperiam, eaque seryu ipsa quae ab illo inventore veritatis et quasi architecto beatae vitae dicta sunt explicabo. Nemo enim ipsam voluptatem quia voluptas sit aspernatur aut odit aut.</p><h4>LUCA FERRANT</h4><div class="role">CEO, LOFTWELL</div><div class="avatar" role="img" aria-label="Client portrait"></div></div>
<div class="tcard" style="left:771px"><p>Sed ut perspiciatis unde omnis iste natus error sit ser voluptatem seraccusantium doloremque laudantium, ser totam rem aperiam, eaque seryu ipsa quae ab illo inventore veritatis et quasi architecto beatae vitae dicta sunt explicabo. Nemo enim ipsam voluptatem quia voluptas sit aspernatur aut odit aut.</p><h4>AREN KOVIC</h4><div class="role">CEO, LOFTWELL</div><div class="avatar" role="img" aria-label="Client portrait"></div></div>
<div class="abs dots" style="left:566px;top:3631px"><span></span><span></span><span class="on" style="background:#222;border-color:#222"></span></div>

<!-- footer -->
<div class="abs footer"></div>
<svg class="abs" style="left:0;top:3690px" width="1200" height="110" viewBox="0 0 1200 110">
  <path d="M0 0 L1200 0 L1200 20 Q600 170 0 20Z" fill="#fff"/>
  <path d="M40 5 Q600 110 1160 5 Q600 80 40 5Z" fill="#3f6fa8"/>
</svg>
<div class="abs f-brand">BRIGHTMOOR LIFT INC</div>
<div class="abs follow">FOLLOW US: <span class="ic"></span><span class="ic"></span><span class="ic"></span><span class="ic"></span></div>
<div class="abs f-line"></div>
<p class="abs f-about">Lorem ipsum dolor sit amet, consectetur adipiscing elit, sed do eiusmod tempor incididunt ut labore Risus commodo viverra maecenas.</p>
<div class="abs f-head" style="left:522px;top:3955px">QUICK LINKS:</div>
<ul class="abs links"><li>Home</li><li>About us</li><li>Our services</li><li>Employees</li><li>More</li></ul>
<div class="abs f-head" style="left:757px;top:3955px">NEWSLETTER:</div>
<div class="abs input">Enter your mail</div>
<div class="btn" style="left:748px;top:4063px;width:172px;height:50px">SUBMIT <svg viewBox="0 0 26 14" style="width:22px;height:18px"><path d="M2 7l22-6-6 12-4-5z" fill="none" stroke="#fff" stroke-width="1.5"/></svg></div>
<div class="abs copy">Copyrights © 2020 Allrights Reserved.</div>

</body>
</html>
```